We are a recruitment company based in Norwich/Cambridge England.
I have included our company logo which we want to remain the same.

What we are looking for is a new creative Business card which will really stand out!!

Contact Information for Business Card

Harriet Dunmore
email: Harriet@plavex.co.uk
Address: Brackwell House
Fenmoor Enterprise Park
Partridge Way
Norwich
QB9 3KX
Tel:01632 960418

```html
<!DOCTYPE html>
<html lang="en">
<head>
<meta charset="utf-8">
<title>Plavex Business Card</title>
<link href="https://fonts.googleapis.com/css2?family=Lato:wght@400;700&display=swap" rel="stylesheet">
<style>
  :root {
    --backdrop: #2a2a2a;
    --paper: #f4f4f3;
    --green: #86bc3c;
    --grey: #7b7c7f;
    --ink: #4a4a4a;
    --faint: #e6e6e4;
    --white: #ffffff;
  }
  * { margin: 0; padding: 0; box-sizing: border-box; }
  html, body {
    width: 1200px; height: 960px; overflow: hidden;
    background: var(--backdrop);
    font-family: "Lato", sans-serif;
  }
  .card {
    position: absolute;
    width: 600px; height: 343px;
    border-radius: 22px;
    overflow: hidden;
  }
  .card-front { left: 314px; top: 113px; background: var(--paper); }
  .card-back { left: 311px; top: 472px; background: var(--green); }

  .faint-mark {
    position: absolute; left: 270px; top: 20px;
    width: 340px; height: 340px; border-radius: 50%;
    background: var(--faint); opacity: .7;
  }

  .brand { position: absolute; display: flex; align-items: center; gap: 12px; }
  .brand-dot { width: 62px; height: 62px; border-radius: 50%; flex: none; }
  .brand-name { font-weight: 700; font-size: 40px; line-height: 1; letter-spacing: -.5px; }
  .brand-tagline {
    display: block; font-size: 8px; font-weight: 400; letter-spacing: 1.6px;
    margin-top: 4px;
  }
  .card-front .brand { left: 38px; top: 47px; }
  .card-front .brand-dot { background: var(--green); }
  .card-front .brand-name, .card-front .brand-tagline { color: var(--grey); }

  .holder { position: absolute; right: 46px; top: 66px; text-align: right; }
  .holder-name { color: var(--green); font-size: 24px; font-weight: 400; line-height: 1.1; }
  .holder-role { color: var(--grey); font-size: 15px; line-height: 1.2; }
  .tab { position: absolute; right: 0; top: 69px; width: 17px; height: 40px; background: var(--green); }
  .rule { position: absolute; left: 38px; top: 126px; width: 516px; height: 1px; background: var(--green); opacity: .8; }

  .contacts { position: absolute; left: 76px; top: 164px; list-style: none; color: var(--ink); font-size: 14px; line-height: 19px; }
  .contacts li { display: flex; gap: 10px; }
  .contacts li.address { margin-bottom: 9px; }
  .contacts svg { width: 13px; height: 13px; flex: none; margin-top: 3px; fill: var(--green); }

  .card-back .brand { left: 50%; top: 132px; transform: translateX(-50%); }
  .card-back .brand-dot { background: var(--white); }
  .card-back .brand-name, .card-back .brand-tagline { color: var(--white); }
  .site {
    position: absolute; left: 0; right: 0; top: 290px; text-align: center;
    color: var(--white); font-size: 14px; letter-spacing: 6px;
  }
</style>
</head>
<body>
  <section class="card card-front">
    <div class="faint-mark"></div>
    <div class="brand">
      <span class="brand-dot"></span>
      <div><span class="brand-name">Plavex</span><span class="brand-tagline">Technology Recruitment</span></div>
    </div>
    <div class="holder">
      <p class="holder-name">HARRIET DUNMORE</p>
      <p class="holder-role">CEO/FOUNDER</p>
    </div>
    <div class="tab"></div>
    <div class="rule"></div>
    <ul class="contacts">
      <li class="address">
        <svg viewBox="0 0 12 12"><path d="M6 0a4 4 0 0 0-4 4c0 3 4 8 4 8s4-5 4-8a4 4 0 0 0-4-4zm0 5.5A1.5 1.5 0 1 1 6 2.5a1.5 1.5 0 0 1 0 3z"/></svg>
        <span>Brackwell House, Fenmoor Enterprise Park<br>Partridge Way, Norwich QB9 3KX</span>
      </li>
      <li>
        <svg viewBox="0 0 12 12"><path d="M2.5 0.5l2 2.5-1.2 1.4a7 7 0 0 0 4.3 4.3L9 7.5l2.5 2-1.3 2C5.5 11.5 .5 6.5.5 1.8z"/></svg>
        <span>01632 960418</span>
      </li>
      <li>
        <svg viewBox="0 0 12 12"><path d="M3 0h6v12H3zm1 1.5v8h4v-8zM5.5 10.3h1v1h-1z"/></svg>
        <span>01632 960527</span>
      </li>
      <li>
        <svg viewBox="0 0 12 12"><path d="M3 0h6v3H3zM0 4h12v5h-2v3H2V9H0zm3 4v3h6V8z"/></svg>
        <span>01632 960733</span>
      </li>
      <li>
        <svg viewBox="0 0 12 12"><path d="M0 2h12v1L6 7 0 3zm0 2.2l6 4 6-4V10H0z"/></svg>
        <span>Harriet@plavex.co.uk</span>
      </li>
      <li>
        <svg viewBox="0 0 12 12"><circle cx="6" cy="6" r="6"/></svg>
        <span>www.plavex.co.uk</span>
      </li>
    </ul>
  </section>

  <section class="card card-back">
    <div class="brand">
      <span class="brand-dot"></span>
      <div><span class="brand-name">Plavex</span><span class="brand-tagline">Technology Recruitment</span></div>
    </div>
    <p class="site">www.plavex.co.uk</p>
  </section>
</body>
</html>
```